Suds Haven Laundromat Wordpress Design

We need a Wordpress website design for our laundromat, Suds Haven Atlanta, at www.sudshavenatlanta-example.com. We would like to have 6 pages: Home, About Us, Services, Locations, Reviews and Contact us. We will provide content for the text on each page. What we do: We are a full service laundromat that provides dry cleaning drop off, professional laundry services, wash dry fold and self service laundry to the local community. We would like to use the color scheme from our logo to convey a warm, safe, and bright business that caters to its diverse community.
Updates

I like the structure of this laundromat website: http://www.washtroveusa-example.com/ Using my logo and color scheme in the above referenced website is what. Am looking for. The photos attached to the project with the female model should be used as a primary focus and supplemented by actual photos of the equipment.

Target Market(s)

Our target market is a diverse group of people from Midtown Atlanta - LGBTQ community /Locals/Regulars that have been coming to laundromat for 30 years.

Industry/Entity Type

Laundromat

Coding

Coded - Design and coding required

Number of Pages Required

5+ page

Font styles to use
Sans Serif

Colors
0054AA
0677BA
7BADD7
CADEEF
E8F1F8

Requirements
Must have
• Feature this video on the main page: https://videohost-example.com/xq7Rm2bPz4k

```html
<!DOCTYPE html>
<html lang="en">
<head>
<meta charset="utf-8">
<title>Suds Haven Atlanta</title>
<link href="https://fonts.googleapis.com/css2?family=Lobster&family=Montserrat:ital,wght@0,400;0,500;0,600;0,700;1,400&display=swap" rel="stylesheet">
<style>
:root{
  --red:#d10a0a;
  --navy:#04336b;
  --ink:#0b2a55;
  --mint:#e2fbfc;
  --paper:#f3f4f6;
  --grey:#8a8f99;
  --white:#ffffff;
}
*{box-sizing:border-box;margin:0;padding:0}
html,body{width:1200px;height:3173px;overflow:hidden}
body{position:relative;background:var(--paper);font-family:"Montserrat",sans-serif;color:var(--ink)}
.abs{position:absolute}
.script{font-family:"Lobster",cursive;font-weight:400}
.photo{position:absolute;overflow:hidden}
.btn{position:absolute;height:38px;width:113px;border:1.5px solid var(--ink);background:var(--white);font-size:12px;font-weight:600;display:flex;align-items:center;justify-content:center;color:var(--ink);box-shadow:2px 2px 0 var(--ink)}
.btn.red{border-color:var(--red);color:var(--red);box-shadow:2px 2px 0 var(--red)}

/* header */
.site-header{position:absolute;left:0;top:0;width:1200px;height:75px;background:var(--mint)}
.brand{position:absolute;left:88px;top:12px;display:flex;align-items:center;gap:8px;font-family:"Lobster",cursive;color:var(--red);font-size:26px;line-height:1}
.brand-dot{width:14px;height:14px;border-radius:50%;background:var(--red)}
.main-nav{position:absolute;left:472px;top:30px;display:flex;gap:20px;font-size:11.5px;font-weight:500;color:var(--ink)}
.main-nav .active{color:var(--red)}
.header-phone{position:absolute;left:820px;top:27px;display:flex;align-items:center;gap:6px;font-family:"Lobster",cursive;color:var(--red);font-size:16px}
.header-cta{left:963px;top:18px;height:38px;width:113px}

/* hero */
.hero-title{position:absolute;left:0;width:1200px;top:370px;text-align:center;color:var(--white);font-size:38px}
.hero-sub{position:absolute;left:340px;width:520px;top:418px;text-align:center;color:var(--white);font-size:21px;line-height:27px}

/* sections */
.section-title{position:absolute;left:0;width:1200px;text-align:center;color:var(--ink);font-size:38px}
.service{position:absolute;width:260px;text-align:center}
.service-photo{width:198px;height:198px;border-radius:50%;margin:0 auto;border:2px solid var(--red);padding:4px;background:var(--white)}
.service-photo div{width:100%;height:100%;border-radius:50%}
.service h3{margin-top:16px;font-size:14.5px;font-weight:600;color:var(--ink)}
.service p{margin:18px auto 0;width:250px;font-size:9.5px;line-height:15px;color:var(--grey)}

.about{position:absolute;left:0;top:1214px;width:1200px;height:486px;background:var(--navy)}
.about h2{position:absolute;left:88px;top:82px;color:var(--white);font-size:37px;line-height:51px}
.about p{position:absolute;left:88px;top:196px;width:632px;color:var(--white);font-size:9.8px;line-height:15px}
.checks{position:absolute;top:266px;list-style:none;color:var(--white);font-size:10.5px;font-weight:600}
.checks li{height:18.7px;display:flex;align-items:center;gap:9px}
.about .btn{left:88px;top:357px;background:transparent;color:var(--white);border-color:var(--white);box-shadow:2px 2px 0 var(--white)}

.review{position:absolute;top:1822px;width:250px;height:275px;background:var(--white);padding:22px 18px}
.review .quote{font-family:"Lobster",cursive;color:var(--red);font-size:34px;line-height:34px}
.review p{margin-top:8px;font-size:10px;font-style:italic;line-height:18.7px;color:var(--grey)}
.review h4{margin-top:16px;font-size:11px;font-weight:600;color:var(--ink)}
.review span{font-size:10px;color:var(--ink)}

.gal-arrow{position:absolute;top:2498px;width:37px;height:37px;border-radius:50%;border:1.5px solid var(--red);display:flex;align-items:center;justify-content:center}

/* footer */
.footer-col h5{font-family:"Lobster",cursive;font-weight:400;font-size:15px;color:var(--ink);margin-bottom:14px}
.footer-col{position:absolute;top:2928px;font-size:10px;color:var(--ink)}
.links{list-style:none;line-height:18.6px}
.contact-row{display:flex;gap:10px;align-items:flex-start;margin-bottom:9px;line-height:15px}
.newsletter-input{width:181px;height:24px;background:#6b7f98;color:var(--white);font-size:8.5px;padding:7px 12px;margin-top:14px}
.footer-col .btn{position:relative;margin-top:14px;height:24px;width:100px;font-size:11px}
.copyright{position:absolute;left:200px;top:3132px;font-size:9px;color:var(--grey)}
.copyright b{color:var(--red);font-weight:500}
.social{position:absolute;top:3126px;width:25px;height:25px;border-radius:50%}
</style>
</head>
<body>

<!-- hero imagery -->
<svg class="abs" style="left:0;top:0" width="1200" height="630" viewBox="0 0 1200 630">
  <defs>
    <linearGradient id="heroFill" x1="0" y1="0" x2="0" y2="1">
      <stop offset="0" stop-color="#7f9aa0"/>
      <stop offset="0.55" stop-color="#5b6b70"/>
      <stop offset="1" stop-color="#2f3a3f"/>
    </linearGradient>
  </defs>
  <path d="M0 75 H1200 V472 C950 472 820 605 600 605 C380 605 250 472 0 472 Z" fill="url(#heroFill)" role="img" aria-label="Laundromat interior with rows of washers and a woman in a blue dress"/>
  <path d="M0 466 C250 466 380 600 600 600 C820 600 950 466 1200 466 V474 C950 474 820 616 600 616 C380 616 250 474 0 474 Z" fill="var(--red)"/>
  <path d="M600 536 V556 M592 548 L600 556 L608 548" stroke="var(--white)" stroke-width="2" fill="none"/>
</svg>

<header class="site-header">
  <div class="brand"><span class="brand-dot"></span>The Suds Haven</div>
  <nav class="main-nav">
    <span class="active">Home</span><span>About Us</span><span>Services</span><span>Locations</span><span>Reviews</span>
  </nav>
  <div class="header-phone">
    <svg width="14" height="14" viewBox="0 0 24 24"><path d="M5 3h4l2 5-3 2a12 12 0 0 0 6 6l2-3 5 2v4a2 2 0 0 1-2 2A18 18 0 0 1 3 5a2 2 0 0 1 2-2z" fill="none" stroke="var(--red)" stroke-width="2"/></svg>
    404-555-0148
  </div>
  <div class="btn red header-cta">Contact Us</div>
</header>

<h1 class="hero-title script">Laundromat for 30 Years</h1>
<p class="hero-sub">Coin Laundry, Dry Cleaning, and Professional Laundry</p>

<!-- what we do -->
<h2 class="section-title script" style="top:664px">What We Do</h2>

<div class="service" style="left:195px;top:735px">
  <div class="service-photo"><div role="img" aria-label="Woman loading a front-load washer" style="background:radial-gradient(circle at 60% 40%,#c9a07e,#5d7e8e 70%)"></div></div>
  <h3>Dry Cleaning Drop Off</h3>
  <p>It is a long established fact that a reader will be distracted by the readable content of a page when looking at its layout. The point of using Lorem Ipsum is that it has a more-or-less normal ...</p>
</div>
<div class="btn" style="left:269px;top:1062px">Read More</div>

<div class="service" style="left:470px;top:735px">
  <div class="service-photo"><div role="img" aria-label="Woman seated on a chair in front of washers" style="background:linear-gradient(180deg,#dfe3e0,#9aa5a8 60%,#c3c6c4)"></div></div>
  <h3>Professional Laundry Services</h3>
  <p>It is a long established fact that a reader will be distracted by the readable content of a page when looking at its layout. The point of using Lorem Ipsum is that it has a more-or-less normal ...</p>
</div>
<div class="btn red" style="left:544px;top:1062px">Read More</div>

<div class="service" style="left:745px;top:735px">
  <div class="service-photo"><div role="img" aria-label="Woman posing under the shop sign beside washers" style="background:linear-gradient(180deg,#a9d3d4,#8ab3b3 55%,#5a6e72)"></div></div>
  <h3>Wash Dry Fold</h3>
  <p>It is a long established fact that a reader will be distracted by the readable content of a page when looking at its layout. The point of using Lorem Ipsum is that it has a more-or-less normal ...</p>
</div>
<div class="btn" style="left:819px;top:1062px">Read More</div>

<!-- about band -->
<svg class="abs" style="left:0;top:1180px" width="1200" height="36"><path d="M0 3 L600 34 L0 34 Z" fill="var(--red)"/></svg>
<section class="about">
  <h2 class="script">Coin Laundry, Dry Cleaning, &amp;<br>Professional Laundry</h2>
  <p>There are many variations of passages of Lorem Ipsum available, but the majority have suffered alteration in some form, by injected humour, or randomised words which don't look even slightly believable. If you are going to use a passage of Lorem Ipsum, you need to be sure there isn't anything embarrassing hidden in the middle of text.</p>
  <ul class="checks" style="left:88px">
    <li><svg width="13" height="8"><path d="M1 4l3 3 6-6M5 7l7-6" stroke="#fff" fill="none" stroke-width="1.2"/></svg>In Business over 45 years</li>
    <li><svg width="13" height="8"><path d="M1 4l3 3 6-6M5 7l7-6" stroke="#fff" fill="none" stroke-width="1.2"/></svg>Voted "BEST COIN LAUNDRY" - Multiple years</li>
    <li><svg width="13" height="8"><path d="M1 4l3 3 6-6M5 7l7-6" stroke="#fff" fill="none" stroke-width="1.2"/></svg>The best Wash-Dry-Fold in town</li>
    <li><svg width="13" height="8"><path d="M1 4l3 3 6-6M5 7l7-6" stroke="#fff" fill="none" stroke-width="1.2"/></svg>Over 50 well maintained machines</li>
  </ul>
  <ul class="checks" style="left:380px">
    <li><svg width="13" height="8"><path d="M1 4l3 3 6-6M5 7l7-6" stroke="#fff" fill="none" stroke-width="1.2"/></svg>In Business over 45 years</li>
    <li><svg width="13" height="8"><path d="M1 4l3 3 6-6M5 7l7-6" stroke="#fff" fill="none" stroke-width="1.2"/></svg>One of Atlanta's First, Finest, &amp; Friendliest Coin Laundries</li>
    <li><svg width="13" height="8"><path d="M1 4l3 3 6-6M5 7l7-6" stroke="#fff" fill="none" stroke-width="1.2"/></svg>Cool - Comfortable - Clean</li>
    <li><svg width="13" height="8"><path d="M1 4l3 3 6-6M5 7l7-6" stroke="#fff" fill="none" stroke-width="1.2"/></svg>Commercial Accounts</li>
  </ul>
  <div class="btn">About Us</div>
  <div class="abs" style="left:775px;top:61px;width:338px;height:338px;border:1.5px solid var(--red)"></div>
  <div class="photo" style="left:750px;top:87px;width:338px;height:338px;background:linear-gradient(160deg,#8c9aa3,#c9c3b9 50%,#4c5560)" role="img" aria-label="Video still of a customer carrying a laundry basket">
    <svg class="abs" style="left:152px;top:152px" width="34" height="34"><circle cx="17" cy="17" r="15" fill="none" stroke="#fff" stroke-width="2"/><path d="M13 10 L24 17 L13 24 Z" fill="none" stroke="#fff" stroke-width="2"/></svg>
  </div>
</section>
<svg class="abs" style="left:0;top:1700px" width="1200" height="32"><path d="M600 0 H1200 V31 Z" fill="var(--red)"/></svg>

<!-- reviews -->
<h2 class="section-title script" style="top:1752px">Client Reviews</h2>
<div class="review" style="left:200px"><div class="quote">66</div><p>"There are many variations of passages of Lorem Ipsum available, but the majority have suffered alteration in some form, by injected humour, or randomised words which don't look even slightly believable. If you are going to use a passage of Lorem Ipsum, you need to be sure there isn't anything embarrassing"</p><h4>Standard Chunk</h4><span>popular belief</span></div>
<div class="review" style="left:475px"><div class="quote">66</div><p>"There are many variations of passages of Lorem Ipsum available, but the majority have suffered alteration in some form, by injected humour, or randomised words which don't look even slightly believable. If you are going to use a passage of Lorem Ipsum, you need to be sure there isn't anything embarrassing"</p><h4>Standard Chunk</h4><span>popular belief</span></div>
<div class="review" style="left:750px"><div class="quote">66</div><p>"There are many variations of passages of Lorem Ipsum available, but the majority have suffered alteration in some form, by injected humour, or randomised words which don't look even slightly believable. If you are going to use a passage of Lorem Ipsum, you need to be sure there isn't anything embarrassing"</p><h4>Standard Chunk</h4><span>popular belief</span></div>
<div class="btn red" style="left:543px;top:2128px">View All</div>

<!-- gallery -->
<svg class="abs" style="left:0;top:2196px" width="1200" height="34"><path d="M0 0 L740 32 L0 32 Z" fill="var(--red)"/></svg>
<div class="abs" style="left:0;top:2228px;width:1200px;height:660px;background:var(--white)"></div>
<h2 class="section-title script" style="top:2280px">Equipment Gallery</h2>
<div class="photo" style="left:200px;top:2348px;width:388px;height:338px;background:linear-gradient(160deg,#9aa19f,#c7c9c6 45%,#6f7372)" role="img" aria-label="Stainless steel washers in a row"></div>
<div class="photo" style="left:612px;top:2348px;width:387px;height:157px;background:linear-gradient(90deg,#cfd6d6,#9ea7a8)" role="img" aria-label="Long row of front-load washers"></div>
<div class="photo" style="left:612px;top:2529px;width:181px;height:157px;background:linear-gradient(180deg,#a8d3d2,#7c8d8f)" role="img" aria-label="Washers under the shop sign"></div>
<div class="photo" style="left:818px;top:2529px;width:181px;height:157px;background:linear-gradient(180deg,#d4dad8,#9da4a3)" role="img" aria-label="Aisle of washers and dryers"></div>
<div class="gal-arrow" style="left:126px"><svg width="14" height="10"><path d="M13 5H1M5 1L1 5l4 4" stroke="var(--red)" fill="none" stroke-width="1.3"/></svg></div>
<div class="gal-arrow" style="left:1038px"><svg width="14" height="10"><path d="M1 5h12M9 1l4 4-4 4" stroke="var(--red)" fill="none" stroke-width="1.3"/></svg></div>

<!-- footer -->
<svg class="abs" style="left:0;top:2740px" width="1200" height="433" viewBox="0 0 1200 433">
  <path d="M0 148 C260 148 400 12 600 12 C800 12 940 148 1200 148 V433 H0 Z" fill="var(--mint)"/>
  <path d="M0 144 C260 144 400 2 600 2 C800 2 940 144 1200 144 V150 C940 150 800 18 600 18 C400 18 260 150 0 150 Z" fill="var(--red)"/>
  <path d="M600 100 V80 M592 88 L600 80 L608 88" stroke="var(--red)" stroke-width="2" fill="none"/>
  <line x1="200" y1="368" x2="1000" y2="368" stroke="#c9e3e6" stroke-width="1"/>
</svg>

<div class="brand" style="left:200px;top:2940px;font-size:28px"><span class="brand-dot"></span>The Suds Haven</div>

<div class="footer-col" style="left:405px">
  <h5>Contact Us</h5>
  <div class="contact-row" style="font-size:14px"><svg width="12" height="12" viewBox="0 0 24 24"><path d="M5 3h4l2 5-3 2a12 12 0 0 0 6 6l2-3 5 2v4a2 2 0 0 1-2 2A18 18 0 0 1 3 5a2 2 0 0 1 2-2z" fill="none" stroke="var(--red)" stroke-width="2"/></svg>(404) 555-0148</div>
  <div class="contact-row"><svg width="12" height="10" viewBox="0 0 24 18"><rect x="1" y="1" width="22" height="16" fill="none" stroke="var(--red)" stroke-width="2"/><path d="M1 1l11 9 11-9" fill="none" stroke="var(--red)" stroke-width="2"/></svg>sudshavenatlanta@example.com</div>
  <div class="contact-row" style="margin-top:18px"><svg width="10" height="13" viewBox="0 0 20 26"><path d="M10 25S2 15 2 9a8 8 0 0 1 16 0c0 6-8 16-8 16z" fill="none" stroke="var(--red)" stroke-width="2"/><circle cx="10" cy="9" r="3" fill="none" stroke="var(--red)" stroke-width="2"/></svg><span>Maple Row Shopping Center,<br>210 Elmfield Ave NE., # 12, Atlanta,<br>GA 30309</span></div>
</div>

<div class="footer-col" style="left:669px">
  <h5>Quick Links</h5>
  <ul class="links"><li>Home</li><li>About Us</li><li>Services</li><li>Locations</li><li>Reviews</li><li>Contact Us</li></ul>
</div>

<div class="footer-col" style="left:818px;width:185px">
  <h5>Sign Up Newsletter</h5>
  <p style="line-height:15px">There are many variations of passages lorem Ipsum available</p>
  <div class="newsletter-input">Enter your email ...</div>
  <div class="btn red">Read More</div>
</div>

<p class="copyright">© 2021 <b>Suds Haven Atlanta</b> All Right Reserved</p>
<div class="social" style="left:819px;background:var(--navy)"></div>
<div class="social" style="left:850px;background:var(--red)"></div>

</body>
</html>
```